KVM Contracting services . Building and maintenance services, optic fibre installation

Business cards and logo design.I need a logo that I can use on business cards ,workwear and on my vehicles. I would like the KVM to be the main or larger text and contracting services to be the smaller or less important text.I like monograms, modern designs and repeating patterns symbols. I am also a Gemini and my favourite number is 22 so if this can be any inspiration to help with the design. Am thinking of the using German flag colours as a his is my family’s heritage. And the other 2 main colours I wear is black and white.But any ideas are appreciated.I do not need a design that is trade specific but a design that could be used for any business.

Target Market(s)

General public

Contact Information for Business Card

KVM Contracting Services ( front of business card)

(Back of business card)
Darren Holtwick
0451907326
Maintenance services
Optic fibre and data installation

Logo Text

Logo can just be pattern or monogram or incorporate KVM . I like the gemini star sign and the number 22

Colors
ec1f27
000000
fbee3e
ffffff

Requirements
Must have
• Logo and KVM Contracting Services on the front of business card
Nice to have
• Possible use of German flag colours.
• Modern design.
• Design to be able to be used on black or white background as I want to put it on clothing

```html
<!DOCTYPE html>
<html lang="en">
<head>
<meta charset="utf-8">
<title>KVM Contracting Services – Business Card</title>
<link href="https://fonts.googleapis.com/css2?family=Lato:wght@400;700&family=Roboto+Condensed:wght@400&display=swap" rel="stylesheet">
<style>
  :root {
    --backdrop: #2b2a2a;
    --brand-red: #e0262d;
    --card-black: #0a0a0a;
    --card-white: #ffffff;
    --ink: #1a1a1a;
    --ink-soft: #555555;
  }
  * { margin: 0; padding: 0; box-sizing: border-box; }
  html, body { width: 1200px; height: 930px; overflow: hidden; }
  body {
    background: var(--backdrop);
    font-family: "Lato", sans-serif;
    display: flex;
    flex-direction: column;
    align-items: center;
    justify-content: center;
    gap: 40px;
  }
  .card {
    position: relative;
    width: 700px;
    height: 400px;
    border-radius: 22px;
    overflow: hidden;
    box-shadow: 0 14px 30px rgba(0,0,0,0.45);
  }
  .card--front {
    background: linear-gradient(135deg, #181818 0%, var(--card-black) 55%, #000 100%);
    display: flex;
    align-items: center;
    justify-content: center;
  }

  /* Company name placeholder: one colour, one weight, plain square beside it */
  .brand-name {
    display: flex;
    align-items: center;
    gap: 14px;
    color: var(--brand-red);
    font-family: "Lato", sans-serif;
    font-weight: 700;
    line-height: 1;
    white-space: nowrap;
  }
  .brand-name__mark {
    flex: none;
    background: var(--brand-red);
  }
  .card--front .brand-name { font-size: 38px; }
  .card--front .brand-name__mark { width: 30px; height: 30px; }

  .card--back { background: var(--card-white); color: var(--ink); }
  .card--back .brand-name {
    position: absolute;
    left: 48px; top: 64px;
    font-size: 30px;
    gap: 12px;
  }
  .card--back .brand-name__mark { width: 24px; height: 24px; }

  .holder {
    position: absolute;
    right: 52px; top: 188px;
    text-align: right;
  }
  .holder__name {
    font-family: "Roboto Condensed", sans-serif;
    font-size: 32px;
    color: var(--brand-red);
    text-transform: uppercase;
    line-height: 1;
  }
  .holder__role { font-size: 17px; margin-top: 14px; }
  .divider {
    position: absolute;
    left: 40px; right: 52px; top: 232px;
    height: 2px;
    background: var(--ink);
  }
  .contacts {
    position: absolute;
    left: 48px; top: 262px;
    list-style: none;
    font-size: 18px;
    line-height: 1.45;
  }
  .contacts li { display: flex; align-items: center; gap: 10px; }
  .contacts svg { width: 13px; height: 13px; flex: none; }
  .address {
    position: absolute;
    right: 52px; top: 282px;
    text-align: right;
    font-size: 18px;
    line-height: 1.4;
  }
  .services {
    position: absolute;
    left: 48px; right: 52px; bottom: 24px;
    display: flex;
    gap: 18px;
    list-style: none;
    font-size: 13px;
    letter-spacing: 1px;
    text-transform: uppercase;
    color: var(--ink-soft);
  }
  .services li + li::before {
    content: "";
    display: inline-block;
    width: 6px; height: 6px;
    margin-right: 18px;
    vertical-align: middle;
    background: var(--brand-red);
  }
</style>
</head>
<body>
  <section class="card card--front" aria-label="Card front">
    <p class="brand-name"><span class="brand-name__mark" aria-hidden="true"></span>KVM Contracting Services</p>
  </section>

  <section class="card card--back" aria-label="Card back">
    <p class="brand-name"><span class="brand-name__mark" aria-hidden="true"></span>KVM Contracting Services</p>

    <div class="holder">
      <p class="holder__name">Darren Holtwick</p>
      <p class="holder__role">Director</p>
    </div>
    <div class="divider"></div>

    <ul class="contacts">
      <li>
        <svg viewBox="0 0 24 24" aria-hidden="true"><path fill="#e0262d" d="M6.6 10.8a15 15 0 0 0 6.6 6.6l2.2-2.2a1 1 0 0 1 1-.25 11.4 11.4 0 0 0 3.6.57 1 1 0 0 1 1 1V20a1 1 0 0 1-1 1A17 17 0 0 1 3 4a1 1 0 0 1 1-1h3.5a1 1 0 0 1 1 1c0 1.25.2 2.45.57 3.57a1 1 0 0 1-.25 1z"/></svg>
        0451907326
      </li>
      <li>
        <svg viewBox="0 0 24 24" aria-hidden="true"><rect x="2.5" y="5" width="19" height="14" rx="1.5" fill="none" stroke="#e0262d" stroke-width="2.2"/><path d="M3 6l9 7 9-7" fill="none" stroke="#e0262d" stroke-width="2.2"/></svg>
        hello@kvmcontracting.com
      </li>
      <li>
        <svg viewBox="0 0 24 24" aria-hidden="true"><circle cx="12" cy="12" r="9.5" fill="none" stroke="#e0262d" stroke-width="2.2"/><path d="M2.5 12h19M12 2.5c3 3 3 16 0 19M12 2.5c-3 3-3 16 0 19" fill="none" stroke="#e0262d" stroke-width="1.8"/></svg>
        www.kvmcontracting.com
      </li>
    </ul>

    <p class="address">18 Birchwood Rd,<br>Lakeview, FL 32099, USA</p>

    <ul class="services">
      <li>Maintenance services</li>
      <li>Optic fibre and data installation</li>
    </ul>
  </section>
</body>
</html>
```